Web Site Design for a Finance (lending) Company

We are opening a new subsidiary that focuses on lending money in the real estate industry. We need a web site designed to represent the business.

The business is lending money to real estate investors. A typical client/borrower will be looking to borrow money to buy a house, renovate it and then sell it at a profit, all within 12 months or less.

Company name is RTV Finance. Our logo is attached.

Attached is a general outline for the web site. We're working on writing more text for each page but this should give you enough to get started with some ideas.

Competitor web site that I like a lot (as an example): https://dorvaleqcapital.example/. Many of the general items on this site match what we will need (description of loan programs, FAQ)

Target Market(s)

Real estate investors (generally individuals or small companies with just a few people) who are buying homes, renovating them and then selling them at a profit.

Industry/Entity Type

Finance

Coding

Coded - Design and coding required

Number of Pages Required

5+ page

Colors

Designer to choose colors to be used in the design.

Requirements
Must have
• Minimalist design. Clean lines without too much clutter. Some stock photography is ok but the photos should not be distracting. They should almost fade in to the background so that user can focus on the key information about what our company does instead. We are a finance company, not a design company, so the information about our products will be more interesting to site visitors than the art.
• Some minimalist examples from Snapboard:
• https://www.snapboardia.example/explore/minimalist-web-design/
Nice to have
• If you search in zoovle for "hard money lenders" you will find many examples of web sites from our competition. I have provided a link above to competitor web site that I like a lot.
• I have attached our logo in EPS format. Logo is green. Web site doesn't have to be green but it should be of a color that will work well with the logo.

```html
<!DOCTYPE html>
<html lang="en">
<head>
<meta charset="utf-8">
<title>RTV Finance</title>
<link href="https://fonts.googleapis.com/css2?family=Poppins:wght@400;500;600;700&display=swap" rel="stylesheet">
<style>
:root{
  --green:#1f5a32;
  --green-dark:#154026;
  --gray-panel:#a4a6ad;
  --gray-circle:#a9abb1;
  --ink:#2b2b2b;
  --text:#444;
  --muted:#888;
  --footer:#1e1e1e;
  --white:#fff;
}
*{margin:0;padding:0;box-sizing:border-box}
html,body{width:1200px;height:2761px;overflow:hidden}
body{font-family:'Poppins',sans-serif;background:var(--white);color:var(--text);position:relative}

/* header */
.site-header{position:absolute;left:0;top:0;width:1200px;height:135px;background:var(--white)}
.brand{position:absolute;left:100px;top:42px;display:flex;align-items:center;gap:14px}
.brand-square{width:34px;height:34px;background:var(--green)}
.brand-name{font-size:30px;font-weight:600;color:var(--green);letter-spacing:.5px}
.search{position:absolute;left:618px;top:26px;width:215px;height:30px;border:1px solid #bbb;border-radius:15px;font-size:11px;color:#777;padding:6px 14px}
.search svg{position:absolute;right:12px;top:8px}
.phone{position:absolute;left:855px;top:26px;display:flex;align-items:center;gap:10px;font-size:16px;font-weight:500;color:var(--green)}
.main-nav{position:absolute;top:86px;left:530px}
.main-nav a{font-size:15px;color:#333;text-decoration:none;letter-spacing:.5px;position:absolute;white-space:nowrap;top:0}
.main-nav a.active{color:var(--green)}
.nav-underline{position:absolute;left:530px;top:132px;width:48px;height:3px;background:var(--green)}

/* hero */
.hero{position:absolute;left:0;top:135px;width:1200px;height:555px;background:linear-gradient(120deg,#3a3530 0%,#5b5450 40%,#4a4643 70%,#2e2b29 100%)}
.hero-rule{position:absolute;left:300px;width:600px;height:1px;background:rgba(255,255,255,.55)}
.hero h1{position:absolute;left:0;top:205px;width:1200px;text-align:center;color:var(--white);font-size:41px;font-weight:600;line-height:47px;letter-spacing:1px}
.dots{position:absolute;top:462px;left:572px;display:flex;gap:6px}
.dots span{width:14px;height:14px;border-radius:50%;border:2px solid #ddd}
.dots span.on{background:#fff}

/* welcome */
.welcome h2{position:absolute;left:0;top:750px;width:1200px;text-align:center;font-size:43px;font-weight:500;color:var(--ink)}
.welcome h2 span{color:var(--green)}
.welcome p{position:absolute;text-align:center;font-size:15px;line-height:24px;color:#555}

/* loans */
.why-bg{position:absolute;left:0;top:1478px;width:1200px;height:580px;background:linear-gradient(110deg,#3a3634,#2c2a29 55%,#4a4441)}
.panels{position:absolute;left:0;top:1008px}
.panel-copy{position:absolute;text-align:center;color:var(--white)}
.panel-copy h3{font-size:28px;font-weight:600;letter-spacing:1px;margin-top:14px}
.panel-copy p{font-size:12px;line-height:24px;margin-top:10px;opacity:.9}
.btn-outline{display:inline-block;margin-top:22px;border:1px solid rgba(255,255,255,.8);padding:7px 15px;font-size:13px;color:#fff}

/* why */
.why h2{position:absolute;left:0;top:1663px;width:1200px;text-align:center;font-size:32px;font-weight:600;color:var(--white);letter-spacing:1px}
.feature{position:absolute;top:1765px;width:152px;height:152px;border-radius:50%;display:flex;flex-direction:column;align-items:center;justify-content:center;color:var(--white);text-align:center;font-size:14px;font-weight:600;line-height:16px}
.feature.green{background:var(--green)}
.feature.gray{background:var(--gray-circle)}
.feature svg{margin-bottom:10px}

/* membership */
.membership h2{position:absolute;left:0;top:2122px;width:1200px;text-align:center;font-size:34px;font-weight:500;color:var(--ink)}
.member-box{position:absolute;top:2212px;width:191px;height:95px;border:1px solid #d7d7d7;display:flex;align-items:center;justify-content:center}
.member-box span{width:110px;height:34px;background:#d9d9d9;border-radius:4px}
.carousel-arrow{position:absolute;top:2240px}

/* footer */
.site-footer{position:absolute;left:0;top:2392px;width:1200px;height:369px;background:var(--footer);color:#ddd}
.site-footer h4{position:absolute;top:63px;font-size:17px;font-weight:600;color:#fff;letter-spacing:.5px}
.f-line{position:absolute;font-size:13px;line-height:20px;color:#ddd;display:flex;gap:14px;align-items:flex-start}
.signup-text{position:absolute;left:372px;top:102px;width:290px;font-size:11px;line-height:20px;color:#ccc}
.signup-input{position:absolute;left:372px;top:152px;width:285px;height:40px;background:#fff;font-size:11px;color:#777;padding:12px 10px}
.signup-btn{position:absolute;left:372px;top:203px;width:100px;height:40px;background:var(--green);color:#fff;font-size:12px;display:flex;align-items:center;justify-content:center}
.social{position:absolute;left:735px;font-size:13px;color:#ddd;display:flex;align-items:center;gap:10px}
.social i{width:22px;height:22px;border:1px solid #ccc;border-radius:50%;display:inline-block}
.footer-brand{position:absolute;left:902px;top:90px;display:flex;align-items:center;gap:10px}
.footer-brand .brand-square{width:26px;height:26px}
.footer-brand .brand-name{font-size:24px}
.chat{position:absolute;left:900px;top:180px;width:128px;height:70px;background:var(--green);border-radius:10px;color:#fff;font-size:30px;font-weight:700;display:flex;align-items:center;justify-content:center}
.chat:after{content:"";position:absolute;left:18px;bottom:-16px;border-left:16px solid var(--green);border-bottom:16px solid transparent}
.footer-rule{position:absolute;left:0;top:304px;width:1200px;height:1px;background:#333}
.copyright{position:absolute;left:0;top:330px;width:1200px;text-align:center;font-size:12px;color:#ccc}
</style>
</head>
<body>

<header class="site-header">
  <div class="brand"><span class="brand-square"></span><span class="brand-name">RTV Finance</span></div>
  <div class="search">search
    <svg width="12" height="12" viewBox="0 0 12 12"><circle cx="5" cy="5" r="3.5" fill="none" stroke="#444" stroke-width="1.5"/><line x1="7.5" y1="7.5" x2="11" y2="11" stroke="#444" stroke-width="1.5"/></svg>
  </div>
  <div class="phone">
    <svg width="24" height="24" viewBox="0 0 24 24"><circle cx="12" cy="12" r="11" fill="none" stroke="#1f5a32" stroke-width="1.5"/><path d="M8 6.5l2 0 1 3-1.5 1c.8 1.7 1.8 2.7 3.5 3.5l1-1.5 3 1v2c0 .8-.7 1.5-1.5 1.5C10 16.5 7 13.5 6.5 8c0-.8.7-1.5 1.5-1.5z" fill="#1f5a32"/></svg>
    Phone : +90 212 555 0147
  </div>
  <nav class="main-nav">
    <a class="active" style="left:0">HOME</a>
    <a style="left:77px">ABOUT US</a>
    <a style="left:188px">LOANS</a>
    <a style="left:270px">RESOURCES</a>
    <a style="left:394px">BLOG</a>
    <a style="left:467px">CONTACT US</a>
  </nav>
  <div class="nav-underline"></div>
</header>

<section class="hero" role="img" aria-label="Photo of colleagues reviewing financial charts at a desk, darkened">
  <div class="hero-rule" style="top:195px"></div>
  <h1>LOCAL REAL ESTATE<br>EXPERTS LENDING TO LOCAL<br>REAL ESTATE INVESTORS</h1>
  <div class="hero-rule" style="top:365px"></div>
  <div class="dots"><span class="on"></span><span></span><span></span></div>
</section>

<section class="welcome">
  <h2>Welcome To <span>RTV Finance</span></h2>
  <p style="top:822px;left:220px;width:760px">RTV Finance is a local business with local knowledge and strong industry relationships. A partner with a wide network who offers value added services.</p>
  <p style="top:884px;left:270px;width:660px">RTV has an established pool of experienced investors available for your real estate investment needs</p>
</section>

<div class="why-bg" role="img" aria-label="Dimmed photo of a man drinking coffee at a table"></div>

<section class="panels">
  <svg width="1200" height="532" viewBox="0 0 1200 532">
    <polygon points="0,55 596,0 596,530 0,470" fill="#1f5a32" role="img" aria-label="Green-tinted photo of a hand passing a money bag"/>
    <polygon points="596,0 1200,55 1200,470 596,530" fill="#a4a6ad" role="img" aria-label="Grey-tinted photo of a city office building"/>
    <line x1="596" y1="0" x2="596" y2="530" stroke="#fff" stroke-width="2"/>
    <polyline points="0,470 596,530 1200,470" fill="none" stroke="#fff" stroke-width="2"/>
  </svg>
  <div class="panel-copy" style="left:98px;top:118px;width:400px">
    <svg width="72" height="58" viewBox="0 0 72 58"><path d="M4 2v52h66" fill="none" stroke="#fff" stroke-width="4"/><path d="M12 44l16-18 10 10 20-22" fill="none" stroke="#fff" stroke-width="4"/><path d="M50 12h12v12" fill="none" stroke="#fff" stroke-width="4"/></svg>
    <h3>FIX AND FLIP LOANS</h3>
    <p>Sed ut perspiciatis unde omnis iste natus error sit voluptatem accusantium doloremque laudantium, totam rem aperiam, eaque ipsa quae ab illo inventore veritatis et quasi architecto beatae vitae dicta sunt explicabo.</p>
    <span class="btn-outline">READ MORE</span>
  </div>
  <div class="panel-copy" style="left:700px;top:98px;width:400px">
    <svg width="80" height="78" viewBox="0 0 80 78"><rect x="10" y="16" width="28" height="58" fill="none" stroke="#fff" stroke-width="4"/><rect x="38" y="4" width="32" height="70" fill="none" stroke="#fff" stroke-width="4"/><g fill="#fff"><rect x="17" y="24" width="6" height="6"/><rect x="26" y="24" width="6" height="6"/><rect x="17" y="36" width="6" height="6"/><rect x="26" y="36" width="6" height="6"/><rect x="17" y="48" width="6" height="6"/><rect x="26" y="48" width="6" height="6"/><rect x="45" y="12" width="6" height="6"/><rect x="56" y="12" width="6" height="6"/><rect x="45" y="24" width="6" height="6"/><rect x="56" y="24" width="6" height="6"/><rect x="45" y="36" width="6" height="6"/><rect x="56" y="36" width="6" height="6"/><rect x="45" y="48" width="6" height="6"/><rect x="56" y="48" width="6" height="6"/></g><line x1="2" y1="75" x2="78" y2="75" stroke="#fff" stroke-width="4"/></svg>
    <h3>COMMERCIAL</h3>
    <p>Sed ut perspiciatis unde omnis iste natus error sit voluptatem accusantium doloremque laudantium, totam rem aperiam, eaque ipsa quae ab illo inventore veritatis et quasi architecto beatae vitae dicta sunt explicabo.</p>
    <span class="btn-outline">READ MORE</span>
  </div>
</section>

<section class="why">
  <h2>WHY BORROW FROM RTV</h2>
  <div class="feature green" style="left:110px">
    <svg width="40" height="40" viewBox="0 0 40 40"><circle cx="20" cy="11" r="9" fill="#fff"/><path d="M4 38c0-10 7-15 16-15s16 5 16 15z" fill="#fff"/></svg>EXPERTS</div>
  <div class="feature gray" style="left:275px">
    <svg width="40" height="40" viewBox="0 0 40 40"><path d="M36 4c-10 0-18 6-22 16l6 6c10-4 16-12 16-22z" fill="#fff"/><path d="M12 18l-8 2 4 4zM22 28l-2 8-4-4zM10 28l-6 8 8-6z" fill="#fff"/></svg>FAST<br>APPROVAL</div>
  <div class="feature green" style="left:441px">
    <svg width="44" height="40" viewBox="0 0 44 40"><rect x="3" y="3" width="38" height="26" rx="2" fill="none" stroke="#fff" stroke-width="4"/><rect x="18" y="29" width="8" height="6" fill="#fff"/><rect x="12" y="34" width="20" height="4" fill="#fff"/></svg>PROFESSIONAL</div>
  <div class="feature gray" style="left:605px">
    <svg width="50" height="40" viewBox="0 0 50 40"><circle cx="25" cy="9" r="7" fill="#fff"/><circle cx="10" cy="13" r="5" fill="#fff"/><circle cx="40" cy="13" r="5" fill="#fff"/><path d="M13 38c0-9 5-13 12-13s12 4 12 13z" fill="#fff"/><path d="M1 36c0-7 4-10 9-10 2 0 4 1 5 2-2 2-3 5-3 8z" fill="#fff"/><path d="M49 36c0-7-4-10-9-10-2 0-4 1-5 2 2 2 3 5 3 8z" fill="#fff"/></svg>A PARTNER</div>
  <div class="feature green" style="left:770px">
    <svg width="40" height="40" viewBox="0 0 40 40"><path d="M2 18L38 3 30 37 19 25z" fill="none" stroke="#fff" stroke-width="3.5" stroke-linejoin="round"/><path d="M19 25l19-22" stroke="#fff" stroke-width="3"/></svg>SELECTIVE</div>
  <div class="feature gray" style="left:934px">
    <svg width="40" height="40" viewBox="0 0 40 40"><path d="M4 4h16l17 17-16 16L4 20z" fill="none" stroke="#fff" stroke-width="3.5" stroke-linejoin="round"/><circle cx="12" cy="12" r="3" fill="#fff"/></svg>COMPETITIVE<br>RATES</div>
</section>

<section class="membership">
  <h2>Our Membership</h2>
  <svg class="carousel-arrow" style="left:52px" width="20" height="40" viewBox="0 0 20 40"><polyline points="18,2 2,20 18,38" fill="none" stroke="#ccc" stroke-width="2"/></svg>
  <div class="member-box" style="left:98px"><span></span></div>
  <div class="member-box" style="left:301px"><span></span></div>
  <div class="member-box" style="left:505px"><span></span></div>
  <div class="member-box" style="left:707px"><span></span></div>
  <div class="member-box" style="left:910px"><span></span></div>
  <svg class="carousel-arrow" style="left:1124px" width="20" height="40" viewBox="0 0 20 40"><polyline points="2,2 18,20 2,38" fill="none" stroke="#ccc" stroke-width="2"/></svg>
</section>

<footer class="site-footer">
  <h4 style="left:98px">CONTACT US</h4>
  <div class="f-line" style="left:98px;top:102px">
    <svg width="16" height="20" viewBox="0 0 16 20"><path d="M8 1a6 6 0 0 0-6 6c0 5 6 12 6 12s6-7 6-12a6 6 0 0 0-6-6z" fill="none" stroke="#ddd" stroke-width="1.5"/><circle cx="8" cy="7" r="2" fill="#ddd"/></svg>
    <span>4821 Larkmoor Place<br>Bellgrove, CA 90000</span></div>
  <div class="f-line" style="left:98px;top:158px">
    <svg width="16" height="16" viewBox="0 0 16 16"><path d="M3 1h3l1.5 4-2 1.2c1 2 2.3 3.3 4.3 4.3l1.2-2 4 1.5v3c0 1-1 2-2 2C6 15 1 10 1 3c0-1 1-2 2-2z" fill="none" stroke="#ddd" stroke-width="1.4"/></svg>
    <span>Phone : 800.555.0192</span></div>
  <div class="f-line" style="left:98px;top:194px">
    <svg width="16" height="14" viewBox="0 0 16 14"><rect x="1" y="1" width="14" height="12" fill="none" stroke="#ddd" stroke-width="1.4"/><polyline points="1,1 8,8 15,1" fill="none" stroke="#ddd" stroke-width="1.4"/></svg>
    <span>info@rtvfinance.example</span></div>

  <h4 style="left:372px">SIGN UP TO RECEIVE EMAIL</h4>
  <p class="signup-text">Excepteur sint occaecat cupidatat non proident, sunt in culpa qui Nemo enim ipsam voluptatem</p>
  <div class="signup-input">Enter Name</div>
  <div class="signup-btn">SUBSCRIBE</div>

  <h4 style="left:735px">SOCIAL</h4>
  <div class="social" style="top:103px"><i></i>Friendlane</div>
  <div class="social" style="top:139px"><i></i>Chirpline</div>
  <div class="social" style="top:175px"><i></i>Zoovle+</div>
  <div class="social" style="top:211px"><i></i>Streamhall</div>

  <div class="footer-brand"><span class="brand-square"></span><span class="brand-name">RTV Finance</span></div>
  <div class="chat">CHAT!</div>

  <div class="footer-rule"></div>
  <p class="copyright">Copyright © RTV Finance 2017. All rights reserved.</p>
</footer>

</body>
</html>
```